Computer Company needs a Business card design

We need a business card design for our business. We assist people to transition to the KVS (Kestrel Vantage Scheme). The Verandal Crown Office-owned kvs™ network is a brand new telecommunications network currently being rolled out across Australia, giving access to a reliable broadband connection. Our niche market will predominantly be domestic customers in the 50+ age bracket. The assistance that we provide is everything from arranging the equipment, arranging the plan and contract term, appointment times, final testing of the network and any tweaks that need to be made. We basically PM the transition from start to finish. The business card design should be minimalist, should communicate loyalty and stability, should be easy to read and clearly explain what we do. We have asked for front and back. However, the back of the card does not have to include much information at all. It could be just a small design, or a repeat of our phone number. Up to you. The attached file only says what is required on the card. It does not specify where to arrange the text, what fonts to use, etc etc. As much as we would like to give you more info, due to our very limited design ability, we are not really able to send you any rough, or otherwise, designs of what we are after. Hopefully the above description is enough for you.

```html
<!DOCTYPE html>
<html lang="en">
<head>
<meta charset="utf-8">
<title>Tallowby Business Card – Front and Back</title>
<link rel="stylesheet" href="https://fonts.googleapis.com/css2?family=Roboto:wght@400;700&display=swap">
<style>
  :root {
    --stage: #2a2a2c;
    --card: #060606;
    --white: #ffffff;
    --blue: #1f84cc;
    --grey: #d6d6d6;
    --rule: #7a7a7a;
  }
  * { margin: 0; padding: 0; box-sizing: border-box; }
  html, body {
    width: 1200px;
    height: 900px;
    overflow: hidden;
    background: var(--stage);
    font-family: "Roboto", Arial, sans-serif;
  }
  .stage {
    position: relative;
    width: 1200px;
    height: 900px;
  }
  .card {
    position: absolute;
    left: 320px;
    width: 560px;
    height: 320px;
    background: var(--card);
    box-shadow: 0 12px 30px rgba(0,0,0,0.45);
    display: flex;
    align-items: center;
  }
  .card--front { top: 90px; justify-content: center; }
  .card--back { top: 490px; padding-left: 48px; }

  .brand {
    display: flex;
    align-items: center;
    gap: 10px;
    white-space: nowrap;
  }
  .brand__square {
    width: 18px;
    height: 18px;
    background: var(--blue);
    flex: none;
  }
  .brand__name {
    color: var(--white);
    font-weight: 700;
    letter-spacing: 2px;
  }
  .card--front .brand__name { font-size: 58px; }
  .card--front .brand__square { width: 24px; height: 24px; }
  .card--back .brand__name { font-size: 34px; }

  .divider {
    width: 1px;
    height: 118px;
    background: var(--rule);
    margin: 0 22px 0 28px;
    flex: none;
  }
  .contact { color: var(--grey); font-size: 14px; white-space: nowrap; }
  .contact__name {
    color: var(--blue);
    font-weight: 700;
    font-size: 20px;
    line-height: 1.1;
  }
  .contact__role { font-size: 14px; margin-bottom: 12px; }
  .contact__row {
    display: flex;
    align-items: center;
    gap: 8px;
    line-height: 1.6;
  }
  .contact__row svg { width: 11px; height: 11px; flex: none; }
</style>
</head>
<body>
<main class="stage">
  <section class="card card--front" aria-label="Card front">
    <div class="brand">
      <span class="brand__square"></span>
      <span class="brand__name">TALLOWBY</span>
    </div>
  </section>

  <section class="card card--back" aria-label="Card back">
    <div class="brand">
      <span class="brand__square"></span>
      <span class="brand__name">TALLOWBY</span>
    </div>
    <span class="divider"></span>
    <div class="contact">
      <p class="contact__name">Neil Hartcombe</p>
      <p class="contact__role">Director</p>
      <p class="contact__row">
        <svg viewBox="0 0 12 12" aria-hidden="true"><path d="M3 1 L5 3.5 L4 5 Q5 7 7 8 L8.5 7 L11 9 L9.5 11 Q5 11 1 5 Q1 2 3 1 Z" fill="#1f84cc"/></svg>
        0455208317
      </p>
      <p class="contact__row">
        <svg viewBox="0 0 12 12" aria-hidden="true"><rect x="1" y="2.5" width="10" height="7" fill="none" stroke="#1f84cc" stroke-width="1.2"/><path d="M1 2.5 L6 6.5 L11 2.5" fill="none" stroke="#1f84cc" stroke-width="1.2"/></svg>
        hello@tallowby.com.au
      </p>
      <p class="contact__row">
        <svg viewBox="0 0 12 12" aria-hidden="true"><circle cx="6" cy="6" r="5" fill="none" stroke="#1f84cc" stroke-width="1.2"/><ellipse cx="6" cy="6" rx="2.2" ry="5" fill="none" stroke="#1f84cc" stroke-width="1"/><path d="M1 6 H11" stroke="#1f84cc" stroke-width="1"/></svg>
        www.tallowby.com.au
      </p>
    </div>
  </section>
</main>
</body>
</html>
```